Varnik Holdings — Business Card Design Brief
Overview
Design a double-sided business card for Varnik Holdings that highlights our two service arms: Varnik Communications (telecommunications) and Varnik Energy (business energy solutions). The card should feel smart and stand out when handed to clients.

Objectives
Showcase our areas of specialty clearly.
Reflect the overall Varnik / Varnik Holdings brand while acknowledging both arms.
Explore using both logos (Communications + Energy) or one unified logo, depending on the design.

Deliverables
One double-sided business card design (front + back).

Content & Copy
Front (preferred): Logo: Varnik / Varnik Holdings
Descriptor: Business Communications | Business Energy
Back:My contact details and company details
Core products: Business Mobile • Telephony • Internet • Business Energy Solutions

Brand & Visual Direction
We have a group logo currently tailored more toward telecoms, plus a separate Varnik Energy logo.
Please explore layouts that use both logos or just one, whichever works best.
Color: I wouldn't mind seeing an option using our the Blue/Purple gradient from our website (varnik-example.co.uk), but also open to non-gradient approaches and other colours..

Overall look: Smart, modern, and distinctive.
Format & Print Specs
Double-sided business card format. (Use a standard size

Must-Haves
Front: Varnik wording or Varnik Holdings wording with atleast 1 logo also on front “Business Communications | Business Energy.”

Back: Contact + company details and core products.
A design that stands out while remaining professional.

Nice-to-Have Options
A gradient version using our site’s Blue/Purple gradient.
A non-gradient version.
A dual-logo treatment versus a single-logo treatment.

Thanks
Owen

```html
<!DOCTYPE html>
<html lang="en">
<head>
<meta charset="utf-8">
<title>Varnik Holdings — Business Card</title>
<link rel="stylesheet" href="https://fonts.googleapis.com/css2?family=Montserrat:wght@400;500;700;800&display=swap">
<style>
  :root {
    --navy: #25216a;
    --navy-text: #221d66;
    --sky: #1ea6e0;
    --blue: #2f74c8;
    --green: #3fae49;
    --lime: #c7d62a;
    --white: #ffffff;
    --ground: #e9eaee;
    --muted: #2b2b3a;
  }
  * { box-sizing: border-box; margin: 0; padding: 0; }
  html, body {
    width: 1200px; height: 875px; overflow: hidden;
    background: var(--ground);
    font-family: "Montserrat", Arial, sans-serif;
  }
  .stage {
    width: 1200px; height: 875px;
    display: flex; flex-direction: column; align-items: center; justify-content: center;
    gap: 40px;
  }
  .card {
    position: relative;
    width: 640px; height: 366px;
    border-radius: 22px;
    overflow: hidden;
    box-shadow: 0 10px 28px rgba(20, 20, 50, 0.18);
  }

  /* Front */
  .card--front { background: var(--navy); }
  .brand-mark {
    position: absolute;
    display: flex; align-items: center; gap: 14px;
    font-weight: 700; font-size: 40px; letter-spacing: 0.5px;
  }
  .brand-mark__dot { width: 56px; height: 56px; border-radius: 50%; }
  .brand-mark--comms { left: 70px; top: 128px; color: var(--sky); }
  .brand-mark--comms .brand-mark__dot { background: var(--blue); }
  .brand-mark--energy { left: 362px; top: 128px; color: var(--green); }
  .brand-mark--energy .brand-mark__dot { background: var(--green); }
  .front-divider {
    position: absolute; left: 320px; top: 110px;
    width: 1px; height: 96px; background: var(--lime);
  }
  .descriptor {
    position: absolute; left: 0; right: 0; top: 262px;
    text-align: center; font-size: 17px; font-weight: 500; letter-spacing: 0.3px;
  }
  .descriptor__comms { color: var(--sky); }
  .descriptor__energy { color: var(--lime); }

  /* Back */
  .card--back { background: var(--white); }
  .back-wave { position: absolute; inset: 0; }
  .brand-lockup {
    position: absolute; display: flex; align-items: center; gap: 8px;
    font-weight: 800; font-size: 26px; color: var(--navy-text); letter-spacing: 0.5px;
  }
  .brand-lockup__dot { width: 24px; height: 24px; border-radius: 50%; }
  .brand-lockup--comms { left: 34px; top: 78px; }
  .brand-lockup--comms .brand-lockup__dot { background: var(--blue); }
  .brand-lockup--energy { left: 196px; top: 78px; }
  .brand-lockup--energy .brand-lockup__dot { background: var(--green); }
  .products {
    position: absolute; left: 40px; top: 130px;
    list-style: none; font-size: 14px; color: var(--muted); line-height: 1.55;
  }
  .products li::before { content: "•"; color: var(--sky); margin-right: 6px; }
  .holder { position: absolute; right: 36px; top: 34px; text-align: right; }
  .holder__name {
    font-weight: 800; font-size: 24px; color: var(--navy-text); letter-spacing: 0.5px;
  }
  .holder__role { font-size: 14px; color: var(--muted); margin-top: 2px; }
  .contact {
    position: absolute; right: 34px; top: 180px; text-align: right;
    color: var(--white); font-size: 13.5px; line-height: 1.65; list-style: none;
  }
  .contact li { display: flex; align-items: center; justify-content: flex-end; gap: 8px; }
  .contact__icon { width: 12px; height: 12px; flex: none; }
  .contact__spacer { width: 12px; flex: none; }
</style>
</head>
<body>
<main class="stage">

  <section class="card card--front" aria-label="Business card front">
    <div class="brand-mark brand-mark--comms">
      <span class="brand-mark__dot"></span>Varnik
    </div>
    <div class="front-divider"></div>
    <div class="brand-mark brand-mark--energy">
      <span class="brand-mark__dot"></span>Varnik
    </div>
    <p class="descriptor">
      <span class="descriptor__comms">Business Communications</span>
      <span class="descriptor__comms"> | </span>
      <span class="descriptor__energy">Business Energy</span>
    </p>
  </section>

  <section class="card card--back" aria-label="Business card back">
    <svg class="back-wave" viewBox="0 0 640 366" width="640" height="366" aria-hidden="true">
      <defs>
        <linearGradient id="wave-stroke" gradientUnits="userSpaceOnUse" x1="0" y1="350" x2="640" y2="80">
          <stop offset="0" stop-color="var(--green)"/>
          <stop offset="0.52" stop-color="var(--green)"/>
          <stop offset="0.7" stop-color="var(--sky)"/>
          <stop offset="1" stop-color="var(--sky)"/>
        </linearGradient>
      </defs>
      <path d="M20,366 C230,368 330,310 400,215 C465,125 530,96 640,94 L640,366 Z" fill="var(--navy)"/>
      <path d="M8,352 C225,362 322,300 392,207 C458,117 522,84 640,81" fill="none" stroke="url(#wave-stroke)" stroke-width="7"/>
    </svg>

    <div class="brand-lockup brand-lockup--comms"><span class="brand-lockup__dot"></span>Varnik</div>
    <div class="brand-lockup brand-lockup--energy"><span class="brand-lockup__dot"></span>Varnik</div>

    <ul class="products">
      <li>Business Mobile</li>
      <li>Telephony</li>
      <li>Internet</li>
      <li>Business Energy Solutions</li>
    </ul>

    <div class="holder">
      <p class="holder__name">DORIAN KELL</p>
      <p class="holder__role">Founder/CEO</p>
    </div>

    <ul class="contact">
      <li>24 Calder Row<span class="contact__spacer"></span></li>
      <li>Leeds England, LS2 7QX<span class="contact__spacer"></span></li>
      <li>+44 0113 555 0187
        <svg class="contact__icon" viewBox="0 0 12 12" aria-hidden="true"><path d="M2.5,1 L4.5,1 L5.3,3.6 L4,4.6 C4.7,6 6,7.3 7.4,8 L8.4,6.7 L11,7.5 L11,9.5 C11,10.3 10.3,11 9.5,11 C5,11 1,7 1,2.5 C1,1.7 1.7,1 2.5,1 Z" fill="var(--sky)"/></svg>
      </li>
      <li>info@varnik-example.co.uk
        <svg class="contact__icon" viewBox="0 0 12 12" aria-hidden="true"><rect x="1" y="2.5" width="10" height="7" rx="1" fill="var(--sky)"/><path d="M1.5,3 L6,6.5 L10.5,3" fill="none" stroke="var(--navy)" stroke-width="1"/></svg>
      </li>
      <li>www.varnik-example.co.uk
        <svg class="contact__icon" viewBox="0 0 12 12" aria-hidden="true"><circle cx="6" cy="6" r="5" fill="none" stroke="var(--sky)" stroke-width="1.2"/><ellipse cx="6" cy="6" rx="2.2" ry="5" fill="none" stroke="var(--sky)" stroke-width="1"/><path d="M1,6 L11,6" stroke="var(--sky)" stroke-width="1"/></svg>
      </li>
    </ul>
  </section>

</main>
</body>
</html>
```